Talvo Pollution Mask Packaging

We need a packaging design for a pollution mask, image of mask attached. Have also attached a file with the exact measurements of the box.
There is also an example of a box attached, we would like a similar type design.
I have also attached the Logo, which should be fairly prominent in design.
The following blurb also needed:
Activated carbon dust mask.
99.999% Filtration
Instructions:
1: Place mask over mouth and nose.
2: Ensure aluminium bridge on top.
3: Adjust Tambix on back to desired tension.
4: Additional Filters sold separately.
Material Description
1: Filter 10% Ammonia
2: N99 Filter Cotton
3: CR Material 100% Neoprene
4: N Cloth 100% Nylon
Other font styles liked:
- RR Beaver

```html
<!DOCTYPE html>
<html lang="en">
<head>
<meta charset="utf-8">
<title>Talvo Activated Carbon Dust Mask – Packaging</title>
<link href="https://fonts.googleapis.com/css2?family=Oswald:wght@400;500;600&family=Quicksand:wght@500&display=swap" rel="stylesheet">
<style>
  :root {
    --green: #8dc21f;
    --charcoal: #353535;
    --black: #1f1f1f;
    --header: #242424;
    --grey-text: #8a8a8a;
    --light-text: #cfcfcf;
    --canvas: #e6e8e2;
  }
  * { box-sizing: border-box; margin: 0; padding: 0; }
  html, body { width: 1200px; height: 1200px; overflow: hidden; }
  body {
    background: var(--canvas);
    font-family: "Oswald", "Arial Narrow", sans-serif;
    position: relative;
  }
  .dieline { position: absolute; left: 30px; top: 200px; width: 1140px; height: 800px; }
  .panel, .header { position: absolute; overflow: hidden; }

  /* hang headers */
  .header { top: 0; height: 200px; background: var(--header); }
  .header-front { left: 0; width: 558px; }
  .header-back { left: 662px; width: 374px; }
  .header-tab {
    position: absolute; right: 0; top: 0; width: 108px; height: 200px;
    background: var(--green);
    display: flex; flex-direction: column; align-items: center; justify-content: center;
  }
  .hang-hole { position: absolute; top: 58px; }
  .header-title { position: absolute; left: 24px; top: 62px; line-height: 1.05; color: var(--green); white-space: nowrap; }
  .header-title .small { font-size: 24px; font-weight: 500; display: block; }
  .header-title .big { font-size: 42px; font-weight: 600; display: block; }
  .header-title .note { font-size: 20px; font-weight: 500; color: #fff; display: block; margin-top: 2px; }

  /* brand lockup */
  .brand { display: flex; flex-direction: column; align-items: center; gap: 6px; }
  .brand-dot { width: 56px; height: 56px; border-radius: 50%; background: var(--green); }
  .brand-name { font-weight: 600; font-size: 30px; letter-spacing: 2px; text-transform: uppercase; color: var(--green); line-height: 1; }
  .brand.on-green .brand-dot { background: var(--charcoal); }
  .brand.on-green .brand-name { color: var(--charcoal); }

  /* body panels */
  .panel { top: 200px; height: 600px; }
  .front { left: 0; width: 450px; background: var(--charcoal); }
  .activity-strip { left: 450px; width: 108px; background: var(--green); padding: 16px 10px; }
  .side { width: 104px; background: var(--green); }
  .side-a { left: 558px; }
  .side-b { left: 1036px; }
  .back { left: 662px; width: 374px; background: var(--black); }

  .mask-window { position: absolute; left: 70px; top: 40px; }
  .front .brand { position: absolute; left: 28px; top: 318px; }
  .front .brand-dot { width: 50px; height: 50px; }
  .front .brand-name { font-size: 26px; }
  .front-title { position: absolute; left: 28px; top: 404px; width: 394px; color: var(--green); line-height: 1; white-space: nowrap; }
  .front-title .line1 { font-size: 40px; font-weight: 600; display: block; }
  .front-title .line2 { font-size: 72px; font-weight: 600; display: block; padding-bottom: 6px; border-bottom: 3px solid var(--green); }
  .front-title .line3 { font-size: 30px; font-weight: 500; color: var(--grey-text); display: block; text-align: right; margin-top: 10px; }

  .strip-title { color: var(--charcoal); line-height: 1.05; white-space: nowrap; }
  .strip-title .small { font-size: 12px; font-weight: 500; display: block; }
  .strip-title .big { font-size: 17px; font-weight: 600; display: block; }
  .activity-icons { list-style: none; margin-top: 30px; display: flex; flex-direction: column; align-items: center; gap: 34px; }
  .activity-icons li { width: 64px; height: 76px; border-radius: 8px; background: var(--charcoal); opacity: .85; }

  .side .brand { position: absolute; left: 0; right: 0; top: 48px; }
  .side-title {
    position: absolute; top: 160px; left: 50%; transform: translateX(-50%);
    writing-mode: vertical-rl; color: var(--charcoal); line-height: .95; white-space: nowrap;
  }
  .side-title .small { font-size: 28px; font-weight: 600; }
  .side-title .big { font-size: 56px; font-weight: 600; }
  .side-rating { position: absolute; bottom: 60px; left: 0; right: 0; text-align: center; color: var(--charcoal); line-height: 1.05; white-space: nowrap; }
  .side-rating .num { font-size: 22px; font-weight: 500; display: block; }
  .side-rating .label { font-size: 17px; font-weight: 500; display: block; }

  .rider-photo {
    position: absolute; left: 0; top: 0; width: 374px; height: 400px;
    background: linear-gradient(160deg, #d6ec9a 0%, #9cc63a 40%, #4d6b1a 75%, #263412 100%);
  }
  .materials {
    position: absolute; left: 80px; top: 430px;
    font-family: "Quicksand", "Helvetica", sans-serif; font-size: 16px; line-height: 1.4; color: var(--light-text);
    white-space: nowrap;
  }
  .materials ol { list-style: none; }
</style>
</head>
<body>
  <main class="dieline">
    <section class="header header-front">
      <h2 class="header-title">
        <span class="small">ACTIVATED CARBON</span>
        <span class="big">DUST MASK</span>
        <span class="note">99.999% FILTRATION</span>
      </h2>
      <svg class="hang-hole" style="left:260px" width="150" height="50" viewBox="0 0 150 50">
        <path d="M8 18 H60 Q62 4 75 4 Q88 4 90 18 H142 Q148 18 148 24 V38 Q148 46 140 46 H10 Q2 46 2 38 V24 Q2 18 8 18 Z" fill="#fff"/>
      </svg>
      <div class="header-tab">
        <div class="brand on-green"><span class="brand-dot"></span><span class="brand-name">Talvo</span></div>
      </div>
    </section>

    <section class="header header-back">
      <svg class="hang-hole" style="left:40px" width="150" height="50" viewBox="0 0 150 50">
        <path d="M8 18 H60 Q62 4 75 4 Q88 4 90 18 H142 Q148 18 148 24 V38 Q148 46 140 46 H10 Q2 46 2 38 V24 Q2 18 8 18 Z" fill="#fff"/>
      </svg>
      <div class="brand" style="position:absolute; left:240px; top:52px;">
        <span class="brand-dot"></span><span class="brand-name">Talvo</span>
      </div>
    </section>

    <section class="panel front">
      <svg class="mask-window" width="300" height="270" viewBox="0 0 300 270" role="img" aria-label="Green activated carbon dust mask seen through the window">
        <defs>
          <linearGradient id="maskFill" x1="0" y1="0" x2="1" y2="1">
            <stop offset="0" stop-color="#a6d23a"/>
            <stop offset="1" stop-color="#c8e27e"/>
          </linearGradient>
        </defs>
        <path d="M30 8 Q150 -4 278 80 Q300 96 284 118 Q200 230 110 262 Q96 268 86 254 Q20 150 6 50 Q2 12 30 8 Z" fill="url(#maskFill)" stroke="#7fae1d" stroke-width="4"/>
      </svg>
      <div class="brand"><span class="brand-dot"></span><span class="brand-name">Talvo</span></div>
      <h1 class="front-title">
        <span class="line1">ACTIVATED CARBON</span>
        <span class="line2">DUST MASK</span>
        <span class="line3">99.999% FILTRATION</span>
      </h1>
    </section>

    <section class="panel activity-strip">
      <p class="strip-title">
        <span class="small">GREAT FOR ALL</span>
        <span class="big">OUTDOOR</span>
        <span class="big">ACTIVITIES</span>
      </p>
      <ul class="activity-icons">
        <li role="img" aria-label="Cycling icon"></li>
        <li role="img" aria-label="Climbing icon"></li>
        <li role="img" aria-label="Canoeing icon"></li>
        <li role="img" aria-label="Hiking icon"></li>
      </ul>
    </section>

    <section class="panel side side-a">
      <div class="brand on-green"><span class="brand-dot"></span><span class="brand-name">Talvo</span></div>
      <p class="side-title"><span class="small">ACTIVATED CARBON</span><br><span class="big">DUST MASK</span></p>
      <p class="side-rating"><span class="num">99.999%</span><span class="label">FILTRATION</span></p>
    </section>

    <section class="panel back">
      <div class="rider-photo" role="img" aria-label="Mountain biker riding over a mossy rock, green toned photo"></div>
      <div class="materials">
        <p>Material Description</p>
        <ol>
          <li>1: Filter 10% Ammonia</li>
          <li>2: N99 Filter Cotton</li>
          <li>3: CR Material 100% Neoprene</li>
          <li>4: N Cloth 100% Nylon</li>
        </ol>
      </div>
    </section>

    <section class="panel side side-b">
      <div class="brand on-green"><span class="brand-dot"></span><span class="brand-name">Talvo</span></div>
      <p class="side-title"><span class="small">ACTIVATED CARBON</span><br><span class="big">DUST MASK</span></p>
      <p class="side-rating"><span class="num">99.999%</span><span class="label">FILTRATION</span></p>
    </section>
  </main>
</body>
</html>
```